Create banners that convert viewers into buyers!

We provide Online Marketing Solutions for small to medium size businesses from web design, Local SEO, Pay-Per-Click, Social Media and Content Marketing. We've been helping local businesses since 2009 and offer a very high level of service that is rarely matched.

Really like to stay colors of logo like banner ad ideas 2 sample.

Would also like to use a photo of a responsive web design as attached image. (you may use a different layout as image provided may be to big for some dimensions)

Sizes needed:
728x90
300x250
480x60
Updates

Add Slogan: We Drive Traffic & Phone Calls!

Slogan: We Drive Phone Calls & Conversions

Target Market(s)

Small to Medium Size businesses: Main businesses we work with are Home Improvement, Lawyers & Physicians

Industry/Entity Type

Marketing

```html
<!DOCTYPE html>
<html lang="en">
<head>
<meta charset="utf-8">
<title>Northpeak Digital Marketing – Display Banners</title>
<link rel="stylesheet" href="https://fonts.googleapis.com/css2?family=Arimo:wght@400;700&family=Open+Sans:wght@400;600&display=swap">
<style>
  :root {
    --page: #ffffff;
    --frame: #1b2740;
    --blue-deep: #0b4fb3;
    --blue-mid: #1a6fd8;
    --blue-bright: #3a95f0;
    --panel-light: #dbe9f8;
    --panel-mid: #9cc3ec;
    --orange: #f47a1f;
    --orange-shadow: rgba(10, 30, 80, 0.75);
    --white: #ffffff;
    --logo-blue: #123d7a;
    --url-ink: #14284a;
    --btn-top: #ffd34a;
    --btn-bottom: #f5a30f;
    --btn-edge: #c27a08;
    --ink: #111111;
  }
  * { margin: 0; padding: 0; box-sizing: border-box; }
  html, body {
    width: 1200px; height: 755px; overflow: hidden;
    background: var(--page);
  }
  .canvas { position: relative; width: 1200px; height: 755px; }

  .banner {
    position: absolute;
    overflow: hidden;
    border: 1px solid var(--frame);
    background:
      radial-gradient(ellipse at 50% 45%, var(--blue-bright) 0%, var(--blue-mid) 45%, var(--blue-deep) 100%);
    font-family: "Open Sans", Arial, sans-serif;
  }
  .banner > * { position: absolute; }

  .headline {
    font-family: "Arimo", Arial, sans-serif;
    font-weight: 700;
    color: var(--orange);
    text-shadow: 1px 2px 2px var(--orange-shadow);
    line-height: 1.15;
    letter-spacing: -0.3px;
    white-space: nowrap;
  }

  .device-shot {
    border-radius: 4px;
    background: linear-gradient(135deg, #2b2f3a 0%, #4a5366 35%, #b83a2a 55%, #d9dde4 75%, #3a3f4c 100%);
    box-shadow: 0 3px 6px rgba(0,0,0,0.45);
  }

  .services { list-style: none; color: var(--white); white-space: nowrap; }
  .services li { position: relative; padding-left: 0.95em; }
  .services li::before {
    content: ""; position: absolute; left: 0; top: 50%;
    transform: translateY(-50%);
    border-left: 0.45em solid var(--orange);
    border-top: 0.3em solid transparent;
    border-bottom: 0.3em solid transparent;
  }

  .brand {
    font-family: "Arimo", Arial, sans-serif;
    font-weight: 700;
    color: var(--logo-blue);
    line-height: 1;
    text-align: center;
    white-space: nowrap;
  }
  .url {
    font-family: "Arimo", Arial, sans-serif;
    color: var(--url-ink);
    text-align: center;
    white-space: nowrap;
    line-height: 1;
  }

  .cta {
    display: flex; align-items: center; justify-content: center; gap: 0.35em;
    background: linear-gradient(to bottom, var(--btn-top), var(--btn-bottom));
    border: 1px solid var(--btn-edge);
    border-radius: 5px;
    box-shadow: 0 2px 3px rgba(0,0,0,0.4);
    font-family: "Arimo", Arial, sans-serif;
    color: var(--ink);
    text-decoration: none;
    white-space: nowrap;
  }
  .cta svg { height: 0.9em; width: auto; }

  /* 300 x 250 */
  .banner--rect { left: 356px; top: 24px; width: 485px; height: 404px; }
  .banner--rect .headline { left: 0; width: 100%; top: 16px; text-align: center; font-size: 40px; }
  .banner--rect .device-shot { left: 6px; top: 132px; width: 266px; height: 182px; }
  .banner--rect .services { left: 288px; top: 168px; font-size: 19px; line-height: 27px; }
  .banner--rect .brand-panel {
    left: 0; top: 320px; width: 100%; height: 84px;
    background: linear-gradient(to right, var(--white) 0%, var(--panel-light) 40%, var(--panel-mid) 75%, var(--blue-mid) 100%);
  }
  .banner--rect .brand { left: 12px; top: 330px; width: 245px; font-size: 22px; }
  .banner--rect .url { left: 12px; top: 380px; width: 245px; font-size: 18px; }
  .banner--rect .cta { left: 274px; top: 344px; width: 184px; height: 47px; font-size: 25px; }

  /* 728 x 90 */
  .banner--leader { left: 13px; top: 451px; width: 1171px; height: 146px; }
  .banner--leader .device-shot { left: 4px; top: 12px; width: 222px; height: 124px; }
  .banner--leader .headline { left: 248px; top: 26px; font-size: 42px; line-height: 49px; }
  .banner--leader .services { left: 712px; top: 14px; font-size: 19px; line-height: 24px; }
  .banner--leader .brand-panel {
    left: 925px; top: 0; width: 246px; height: 100%;
    border-left: 1px solid var(--frame);
    background: linear-gradient(to bottom, var(--panel-light), var(--panel-mid) 60%, var(--blue-bright));
  }
  .banner--leader .brand { left: 935px; top: 14px; width: 226px; font-size: 21px; }
  .banner--leader .url { left: 935px; top: 64px; width: 226px; font-size: 18px; }
  .banner--leader .cta { left: 958px; top: 88px; width: 183px; height: 48px; font-size: 25px; }

  /* 480 x 60 */
  .banner--strip { left: 13px; top: 613px; width: 752px; height: 96px; }
  .banner--strip .device-shot { left: 4px; top: 8px; width: 166px; height: 82px; }
  .banner--strip .headline { left: 180px; top: 12px; font-size: 23px; letter-spacing: -0.5px; }
  .banner--strip .services {
    left: 230px; top: 44px; width: 360px; font-size: 16px; line-height: 21px;
    display: flex; flex-wrap: wrap; column-gap: 9px;
  }
  .banner--strip .brand-panel {
    left: 593px; top: 0; width: 159px; height: 100%;
    border-left: 1px solid var(--frame);
    background: linear-gradient(to bottom, var(--panel-light), var(--panel-mid) 60%, var(--blue-bright));
  }
  .banner--strip .brand { left: 597px; top: 6px; width: 151px; font-size: 14px; }
  .banner--strip .url { left: 597px; top: 43px; width: 151px; font-size: 13px; }
  .banner--strip .cta { left: 621px; top: 62px; width: 120px; height: 31px; font-size: 16px; border-radius: 4px; }
</style>
</head>
<body>
<main class="canvas">

  <section class="banner banner--rect" aria-label="300 by 250 banner">
    <h2 class="headline">We Drive Phone Calls<br>&amp; Conversions</h2>
    <div class="device-shot" role="img" aria-label="Responsive website shown on phone, tablet and desktop screens"></div>
    <ul class="services">
      <li>Web Design</li>
      <li>Local SEO</li>
      <li>Pay-Per-Click</li>
      <li>Social Media</li>
      <li>Content Marketing</li>
    </ul>
    <div class="brand-panel"></div>
    <p class="brand">Northpeak Digital<br>Marketing</p>
    <p class="url">www.northpeakweb.com</p>
    <a class="cta" href="#">
      <svg viewBox="0 0 12 18" aria-hidden="true"><path d="M1 1v14l3.5-3.3 2.6 5.6 2.3-1-2.6-5.6H11z" fill="#111" stroke="#fff" stroke-width="0.8"/></svg>
      Learn More
    </a>
  </section>

  <section class="banner banner--leader" aria-label="728 by 90 banner">
    <div class="device-shot" role="img" aria-label="Responsive website shown on phone, tablet and desktop screens"></div>
    <h2 class="headline">We Drive Phone Calls<br>&amp; Conversions</h2>
    <ul class="services">
      <li>Web Design</li>
      <li>Local SEO</li>
      <li>Pay-Per-Click</li>
      <li>Social Media</li>
      <li>Content Marketing</li>
    </ul>
    <div class="brand-panel"></div>
    <p class="brand">Northpeak Digital<br>Marketing</p>
    <p class="url">www.northpeakweb.com</p>
    <a class="cta" href="#">
      <svg viewBox="0 0 12 18" aria-hidden="true"><path d="M1 1v14l3.5-3.3 2.6 5.6 2.3-1-2.6-5.6H11z" fill="#111" stroke="#fff" stroke-width="0.8"/></svg>
      Learn More
    </a>
  </section>

  <section class="banner banner--strip" aria-label="480 by 60 banner">
    <div class="device-shot" role="img" aria-label="Responsive website shown on phone, tablet and desktop screens"></div>
    <h2 class="headline">We Drive Phone Calls &amp; Conversions</h2>
    <ul class="services">
      <li>Web Design</li>
      <li>Local SEO</li>
      <li>Pay-Per-Click</li>
      <li>Social Media</li>
      <li>Content Marketing</li>
    </ul>
    <div class="brand-panel"></div>
    <p class="brand">Northpeak Digital<br>Marketing</p>
    <p class="url">www.northpeakweb.com</p>
    <a class="cta" href="#">
      <svg viewBox="0 0 12 18" aria-hidden="true"><path d="M1 1v14l3.5-3.3 2.6 5.6 2.3-1-2.6-5.6H11z" fill="#111" stroke="#fff" stroke-width="0.8"/></svg>
      Learn More
    </a>
  </section>

</main>
</body>
</html>
```